Window and GutterCleaning Flyer A5 size double sided.

We need a double sided A5 flyer. Side 1, is for window cleaning, side 2 is for gutter cleaning. Licensed by Borough of Marlow Council.
Phone number 0800 473 1926.
Business address 17 Fallowmere Close, North Brack Edinburgh EH31 4LP.
www.clearpane-hub-services.com
We use a LoftEye Gutter inspection Cam to view your gutters first to see if they need doing.
Window cleaning ; Professional window cleaning services, what we offer, water fed pole window cleaning able to reach windows up to 60 feet.
Conservatory cleaning.
Conservatory roof cleaning.
Fascias & Soffits cleaning.
Excellent Customer Service.
Target Market(s)
domestic houses
Industry/Entity Type
window cleaning
Look and feel
Each slider illustrates characteristics of the customer's brand and the style your logo design should communicate.

```html
<!DOCTYPE html>
<html lang="en">
<head>
<meta charset="utf-8">
<title>ClearPane Hub – Window &amp; Gutter Cleaning Flyer</title>
<link rel="stylesheet" href="https://fonts.googleapis.com/css2?family=Arimo:wght@400;700&family=Roboto+Condensed:wght@300;400&display=swap">
<style>
:root{
  --navy:#2d2a6b;
  --sky:#a9cdee;
  --ink:#2b2b2b;
  --paper:#ffffff;
  --backdrop:#eceae6;
}
*{margin:0;padding:0;box-sizing:border-box}
html,body{width:1200px;height:861px;overflow:hidden;background:var(--backdrop);font-family:"Arimo",Arial,sans-serif;color:var(--ink)}
.flyer{position:absolute;top:61px;width:525px;height:740px;background:var(--paper);overflow:hidden;box-shadow:0 2px 8px rgba(0,0,0,.18)}
.flyer--windows{left:59px}
.flyer--gutters{left:616px}
.abs{position:absolute}
.top-swoosh,.bottom-band{position:absolute;left:0;width:525px}
.top-swoosh{top:0;height:330px}
.bottom-band{bottom:0;height:60px}
.licence{top:14px;right:18px;text-align:right;color:var(--sky);font-size:14px;line-height:22px;font-weight:700;letter-spacing:.3px}
.brand{top:96px;left:15px;color:var(--navy);font-size:26px;font-weight:700;line-height:30px;display:flex;align-items:center;gap:8px;white-space:nowrap}
.brand-mark{width:13px;height:13px;background:var(--navy)}
.headline{top:188px;left:14px;width:480px;color:var(--navy);font-size:16px;font-weight:700;line-height:22px}
.col{top:242px}
.col h3{color:var(--navy);font-size:12.5px;font-weight:700;margin-bottom:6px;white-space:nowrap}
.col p{font-size:11px;line-height:16.7px}
.col--left{left:14px;width:262px}
.col--right{left:298px;width:205px}
.photo{position:absolute}
.contact-addr{top:618px;left:18px;font-size:11px;line-height:14px;color:var(--navy)}
.contact-addr .row{display:flex;align-items:flex-start;gap:9px;margin-bottom:10px}
.contact-addr svg{flex:none}
.phone-block{position:absolute;display:flex;flex-direction:column;align-items:flex-end}
.phone-block .lead{font-size:10px;color:var(--navy);margin-bottom:2px;white-space:nowrap}
.phone-line{display:flex;align-items:center;gap:10px}
.phone-number{font-family:"Roboto Condensed","Arial Narrow",sans-serif;font-weight:400;font-size:30px;color:var(--navy);line-height:32px;white-space:nowrap}
.web{bottom:10px;left:18px;display:flex;align-items:center;gap:8px;color:#fff;font-size:11px}
.intro{top:202px;left:14px;font-size:14px;line-height:22px;white-space:nowrap}
.section-title{color:var(--navy);font-weight:700}
.offer-title{top:253px;left:14px;font-size:16px}
.caption{top:410px;width:166px;text-align:center;font-size:15px;line-height:19px;color:var(--navy)}
.why-title{top:511px;left:14px;font-size:20px}
.why-list{top:544px;left:14px;list-style:none;font-size:11px}
.why-list li{height:27.5px}
.why-list li::before{content:"•";margin-right:5px}
</style>
</head>
<body>

<!-- Side 1: window cleaning -->
<section class="flyer flyer--windows">
  <svg class="top-swoosh" viewBox="0 0 525 330" aria-hidden="true">
    <path d="M0 4 C300 4 480 90 525 250 V0 H0Z" fill="var(--navy)"/>
    <path d="M0 4 C300 4 480 90 525 250 L525 274 C470 100 300 8 0 4Z" fill="var(--sky)"/>
    <path d="M0 0 H525 V4 H0Z" fill="var(--sky)"/>
  </svg>
  <div class="abs licence">Licensed by<br>Borough of Marlow Council</div>
  <div class="abs brand"><span class="brand-mark"></span>ClearPane Hub</div>
  <h2 class="abs headline">Crystal Clear Views, Every Time! Unfortunately we can't use this as it takes a couple of cleans to get perfect results.</h2>
  <div class="abs col col--left">
    <h3>Professional Window Cleaning Services.</h3>
    <p>We offer high-quality window cleaning for homes and businesses, delivering. We only clean domestic properties not businesses. spotless, streak-free results every time. As per last info, can't claim this too.</p>
  </div>
  <div class="abs col col--right">
    <h3>Pure Water Fed Pole System.</h3>
    <p>Our advanced system reaches up to 60 feet high, safely cleaning upper windows from the ground without the need for ladders.</p>
  </div>
  <div class="photo" role="img" aria-label="Squeegee wiping a wet window pane" style="left:0;top:362px;width:157px;height:228px;background:linear-gradient(160deg,#8fa9c8,#5d7ea8)"></div>
  <div class="photo" role="img" aria-label="Brick house front with white windows and porch" style="left:162px;top:362px;width:128px;height:228px;background:linear-gradient(180deg,#a8654c,#8a4e3a)"></div>
  <div class="photo" role="img" aria-label="Water fed pole brush cleaning a white framed window" style="left:297px;top:362px;width:228px;height:228px;background:linear-gradient(150deg,#dfe3e6,#a9b1b7)"></div>
  <div class="contact-addr abs">
    <div class="row">
      <svg width="14" height="18" viewBox="0 0 14 18"><path d="M7 0a7 7 0 0 0-7 7c0 5 7 11 7 11s7-6 7-11a7 7 0 0 0-7-7z" fill="var(--navy)"/><circle cx="7" cy="7" r="2.6" fill="#fff"/></svg>
      <span>17 Fallowmere Close, North Brack<br>Edinburgh EH31 4LP</span>
    </div>
    <div class="row" style="align-items:center">
      <svg width="16" height="12" viewBox="0 0 16 12"><rect width="16" height="12" rx="1" fill="var(--navy)"/><path d="M1 1 L8 7 L15 1" stroke="#fff" stroke-width="1.4" fill="none"/></svg>
      <span>info@clearpane-hub-services.com</span>
    </div>
  </div>
  <div class="phone-block" style="right:18px;top:622px">
    <div class="lead">For More Information Contact Us</div>
    <div class="phone-line">
      <svg width="32" height="32" viewBox="0 0 34 34"><circle cx="17" cy="17" r="15.5" fill="none" stroke="var(--navy)" stroke-width="2"/><path d="M12 9c-2 1-3 3-2 6 2 5 5 9 9 11 2 1 4 0 5-2l-3-3-2 1c-2-1-4-4-5-6l1-2z" fill="var(--navy)"/></svg>
      <span class="phone-number">0800 473 1926</span>
    </div>
  </div>
  <svg class="bottom-band" viewBox="0 0 525 60" aria-hidden="true">
    <path d="M0 14 C120 2 300 4 525 12 V60 H0Z" fill="var(--navy)"/>
    <path d="M60 22 C160 14 260 16 360 22 M390 26 C430 24 470 22 510 24" stroke="#fff" stroke-width="1.5" fill="none"/>
  </svg>
  <div class="abs web">
    <svg width="14" height="14" viewBox="0 0 14 14" fill="none" stroke="#fff" stroke-width="1"><circle cx="7" cy="7" r="6"/><ellipse cx="7" cy="7" rx="2.6" ry="6"/><path d="M1 7h12M2 4h10M2 10h10"/></svg>
    <span>www.clearpane-hub-services.com</span>
  </div>
</section>

<!-- Side 2: gutter cleaning -->
<section class="flyer flyer--gutters">
  <svg class="top-swoosh" viewBox="0 0 525 330" aria-hidden="true">
    <path d="M0 4 C300 4 480 90 525 250 V0 H0Z" fill="var(--navy)"/>
    <path d="M0 4 C300 4 480 90 525 250 L525 274 C470 100 300 8 0 4Z" fill="var(--sky)"/>
    <path d="M0 0 H525 V4 H0Z" fill="var(--sky)"/>
  </svg>
  <div class="abs licence">Licensed by<br>Borough of Marlow Council</div>
  <div class="abs brand"><span class="brand-mark"></span>ClearPane Hub</div>
  <div class="phone-block" style="left:216px;top:128px">
    <div class="lead">For More Information Contact Us</div>
    <div class="phone-line">
      <svg width="32" height="32" viewBox="0 0 34 34"><circle cx="17" cy="17" r="15.5" fill="none" stroke="var(--navy)" stroke-width="2"/><path d="M12 9c-2 1-3 3-2 6 2 5 5 9 9 11 2 1 4 0 5-2l-3-3-2 1c-2-1-4-4-5-6l1-2z" fill="var(--navy)"/></svg>
      <span class="phone-number">0800 473 1926</span>
    </div>
  </div>
  <p class="abs intro">Gutters are an important part of your home. So why not set up an annual<br>plan &amp; make sure you don't run into problems when winter comes.</p>
  <h2 class="abs section-title offer-title">We Also Offer</h2>
  <div class="photo" role="img" aria-label="White uPVC conservatory on a brick house" style="left:0;top:278px;width:166px;height:127px;background:linear-gradient(180deg,#b9c4ce,#9a6a55)"></div>
  <div class="photo" role="img" aria-label="Polycarbonate conservatory roof panels" style="left:179px;top:278px;width:166px;height:127px;background:linear-gradient(150deg,#7f8a6a,#c4c8c8)"></div>
  <div class="photo" role="img" aria-label="House eaves showing gutter, fascia and soffit" style="left:359px;top:278px;width:166px;height:127px;background:linear-gradient(160deg,#f2f1ee,#b7826a)"></div>
  <div class="abs caption" style="left:0">Conservatory<br>Cleaning</div>
  <div class="abs caption" style="left:179px">Conservatory<br>Roof Cleaning</div>
  <div class="abs caption" style="left:359px">Fascias And<br>Soffits Cleaning</div>
  <h2 class="abs section-title why-title">Why Choose Us?</h2>
  <ul class="abs why-list">
    <li>Friendly, Professional Service</li>
    <li>Reliable And Efficient</li>
    <li>Fully Licensed And Insured</li>
    <li>Excellent Customer Satisfaction</li>
  </ul>
  <div class="photo" role="img" aria-label="LoftEye gutter inspection camera monitor" style="left:192px;top:468px;width:148px;height:105px;background:linear-gradient(160deg,#3a3a3a,#1f1f1f)"></div>
  <div class="photo" role="img" aria-label="Vacuum hose clearing debris from a gutter" style="left:242px;top:573px;width:120px;height:102px;background:linear-gradient(170deg,#c9c9c4,#6e6353)"></div>
  <div class="photo" role="img" aria-label="Gutter vacuum pole beside a lawn and roof" style="left:362px;top:477px;width:161px;height:198px;background:linear-gradient(170deg,#8bb06a,#5f6f4c)"></div>
  <svg class="bottom-band" viewBox="0 0 525 60" aria-hidden="true">
    <path d="M0 14 C120 2 300 4 525 12 V60 H0Z" fill="var(--navy)"/>
    <path d="M60 22 C160 14 260 16 360 22 M390 26 C430 24 470 22 510 24" stroke="#fff" stroke-width="1.5" fill="none"/>
  </svg>
  <div class="abs web">
    <svg width="14" height="14" viewBox="0 0 14 14" fill="none" stroke="#fff" stroke-width="1"><circle cx="7" cy="7" r="6"/><ellipse cx="7" cy="7" rx="2.6" ry="6"/><path d="M1 7h12M2 4h10M2 10h10"/></svg>
    <span>www.clearpane-hub-services.com</span>
  </div>
</section>

</body>
</html>
```